BrambleForge Development Studio Website

We'd like to create a brand new website for our company, so we can display our portfolio, our team, and our general approach to the app development work that we do. We've attached the website content + portfolio images for your convenience.

Our company is focused on substance over glamour, so we want our website to represent that mentality. We need something simple, and clean. We're open to both minimalist designs and as well as bolder designs.

Target Market(s)

Businesses: Startups and established companies

Coding

Coded - Design and coding required

Number of Pages Required

2 page

Font styles to use
Sans Serif

Colors
f78f20
faa54b
ffffff

Requirements
Must have
• We'd like this project to incorporate an orange highlight colour (#FFA300), but otherwise be more or less, black and white. If you'd like to also add a primary colour in your design (outside of the orange and grayscale colours), we're happy to explore it!

NOTICE: At the top of the portfolio section, we'd like a full banner highlighted section for Kelpwarden (a SaaS platform owned and operated by BrambleForge).
Nice to have
• We want the website design to be more on the clean side, for example, look at the portfolio section from: https://www.quillandmarsh.co.uk/ (ignore the top banner).

We're also open to exploring bold designs, something like: https://ferret.net/

```html
<!DOCTYPE html>
<html lang="en">
<head>
<meta charset="utf-8">
<title>BrambleForge Development Studio</title>
<link href="https://fonts.googleapis.com/css2?family=Poppins:wght@400;500;600;700&family=Roboto:wght@400;500&display=swap" rel="stylesheet">
<style>
:root{
  --orange:#f78f20;
  --orange-light:#faa54b;
  --orange-pale:#fde3c4;
  --ink:#1d1d1f;
  --text:#4a4a4a;
  --muted:#8a8a8a;
  --line:#e6e6e6;
  --grey-bg:#f6f6f6;
  --white:#ffffff;
  --footer:#ffffff;
}
*{box-sizing:border-box;margin:0;padding:0}
html,body{width:1200px;height:3504px;overflow:hidden}
body{background:var(--white);font-family:'Roboto',Arial,sans-serif;color:var(--text);position:relative}
.section{position:absolute;left:0;width:1200px}
h1,h2,h3,h4,.brand,.btn{font-family:'Poppins',Arial,sans-serif}
.brand{font-weight:700;font-size:22px;color:var(--ink);display:flex;align-items:center;gap:8px}
.brand-mark{width:14px;height:14px;background:var(--orange);border-radius:50%}
.btn{display:inline-block;background:var(--orange);color:var(--white);font-size:13px;font-weight:600;padding:10px 22px;border-radius:20px;text-transform:uppercase;letter-spacing:.5px}
.btn-outline{background:var(--white);color:var(--orange);border:2px solid var(--white);border-radius:6px;text-transform:none;font-size:16px;padding:12px 28px}
.eyebrow{font-family:'Poppins',sans-serif;font-size:15px;color:var(--ink);font-weight:500}
.section-title{font-size:42px;font-weight:700;color:var(--ink);line-height:1.1}
.center-title{text-align:center;font-size:36px;font-weight:600;color:var(--ink)}
.arrows{position:absolute;display:flex;gap:18px}
.arrows svg{width:34px;height:14px}
.illustration{position:absolute;border-radius:20px}

/* hero */
.hero{top:0;height:540px;border-bottom:1px solid var(--line)}
.hero .brand{position:absolute;left:64px;top:40px}
.hero-blob{position:absolute;right:0;top:0}
.hero .nav-btn{position:absolute;right:64px;top:36px;background:var(--white);color:var(--orange);font-size:11px;padding:8px 18px}
.hero-copy{position:absolute;left:64px;top:210px;width:520px}
.hero-copy .lead{font-family:'Poppins',sans-serif;font-size:24px;font-weight:600;color:var(--ink);margin-bottom:6px}
.hero-copy h1{font-size:38px;font-weight:700;color:var(--ink);line-height:1.25;margin-bottom:26px}
.hero-art{left:660px;top:70px;width:420px;height:420px;background:linear-gradient(150deg,#fff4e6,#ffd6a3)}

/* portfolio */
.portfolio{top:540px;height:440px;border-bottom:1px solid var(--line)}
.portfolio .shot{left:60px;top:60px;width:560px;height:300px;border-radius:4px;background:linear-gradient(180deg,#eef1f4,#dfe4ea);box-shadow:0 8px 24px rgba(0,0,0,.12)}
.portfolio-copy{position:absolute;left:680px;top:80px;width:460px}
.portfolio-copy .section-title{margin-bottom:12px}
.portfolio-copy h3{font-size:24px;font-weight:700;color:var(--ink);line-height:1.3;margin-bottom:12px}
.portfolio-copy .tags{font-family:'Poppins',sans-serif;font-weight:600;font-size:15px;color:var(--ink);margin-bottom:18px}
.portfolio .arrows{left:1030px;top:372px}

/* about */
.about{top:980px;height:380px;border-bottom:1px solid var(--line)}
.about-copy{position:absolute;left:200px;top:100px;width:340px}
.about-copy .section-title{margin-bottom:14px;font-size:40px}
.about-copy p{font-size:14px;line-height:1.55}
.about .art{left:600px;top:50px;width:400px;height:270px;border-radius:50% 45% 50% 40%;background:radial-gradient(circle at 50% 50%,#ffe3bf,#f4ecfb 70%)}

/* approach */
.approach{top:1360px;height:540px;background:var(--grey-bg)}
.approach .center-title{position:absolute;top:56px;width:100%}
.approach .art{left:130px;top:150px;width:440px;height:330px;background:linear-gradient(160deg,#fbe9d3,#f2f2f2)}
.approach-list{position:absolute;left:680px;top:170px;width:390px;list-style:none}
.approach-list li{margin-bottom:16px;font-size:12.5px;line-height:1.45}
.approach-list strong{font-family:'Poppins',sans-serif;color:var(--ink);font-size:14px;font-weight:600}

/* testimonials */
.testimonials{top:1900px;height:540px}
.testimonials .center-title{position:absolute;top:64px;width:100%}
.testimonials .sub{position:absolute;top:118px;width:100%;text-align:center;font-size:14px}
.cards{position:absolute;left:180px;top:180px;display:flex;gap:60px}
.card{width:240px;height:250px;background:var(--white);box-shadow:0 4px 20px rgba(0,0,0,.1);padding:30px 24px 20px;position:relative;text-align:center}
.card .quote{position:absolute;left:18px;top:18px;width:18px;height:14px}
.card p{font-size:12px;line-height:1.55;text-align:left;margin-bottom:12px}
.card .who{font-family:'Poppins',sans-serif;font-size:12px;color:var(--ink);font-weight:600}
.card .role{font-size:11px;color:var(--muted);margin-bottom:4px}
.stars{color:var(--orange);font-size:14px;letter-spacing:2px}
.testimonials .arrows{left:890px;top:452px}

/* team */
.team{top:2440px;height:560px;background:var(--grey-bg)}
.team .center-title{position:absolute;top:60px;width:100%}
.team .intro{position:absolute;top:112px;left:280px;width:640px;text-align:center;font-size:14px;line-height:1.5}
.team .photo{left:140px;top:220px;width:320px;height:210px;border-radius:4px;background:linear-gradient(160deg,#d8dde3,#8e96a1)}
.member{position:absolute;left:500px;top:230px;width:420px}
.member h4{font-size:17px;color:var(--ink);font-weight:600;margin-bottom:14px}
.member p{font-size:14px;line-height:1.6}
.team .arrows{left:880px;top:470px}

/* cta */
.cta{top:3000px;height:160px;background:var(--orange)}
.cta h2{position:absolute;left:100px;top:34px;color:var(--white);font-size:34px;font-weight:600}
.cta p{position:absolute;left:100px;top:90px;width:560px;color:var(--white);font-size:13px;line-height:1.5}
.cta .btn{position:absolute;right:100px;top:54px}

/* footer */
.footer{top:3160px;height:280px}
.footer .shape{position:absolute;left:0;top:0}
.foot-col{position:absolute;top:50px;font-size:13px;line-height:1.9}
.foot-col h4{font-size:15px;color:var(--ink);font-weight:600;margin-bottom:8px;text-transform:uppercase}
.foot-brand{left:100px;width:320px}
.foot-brand .brand{margin-bottom:10px;margin-top:22px}
.foot-brand p{font-size:13px;line-height:1.5}
.foot-links{left:490px}
.foot-contact{left:690px}
.foot-social{left:900px}
.socials{display:flex;gap:10px;margin-top:4px}
.socials span{width:22px;height:22px;border-radius:50%;background:var(--ink);display:block}
.bottom-bar{top:3440px;height:64px;background:var(--orange);display:flex;align-items:center;justify-content:center;color:var(--white);font-size:13px}
</style>
</head>
<body>

<header class="section hero">
  <svg class="hero-blob" width="640" height="520" viewBox="0 0 640 520" aria-hidden="true">
    <path d="M120 0 H640 V360 C560 430 470 330 380 370 C280 420 220 340 200 260 C180 170 70 120 120 0Z" fill="var(--orange-light)"/>
  </svg>
  <div class="brand"><span class="brand-mark"></span>BrambleForge</div>
  <span class="btn nav-btn">Get in touch</span>
  <div class="hero-copy">
    <p class="lead">Digital Products by Experienced Entrepreneurs</p>
    <h1>Where Software Engineering and Business Strategy Collide</h1>
    <span class="btn">Read more</span>
  </div>
  <div class="illustration hero-art" role="img" aria-label="Illustration of a team presenting charts on a large board"></div>
</header>

<section class="section portfolio">
  <div class="illustration shot" role="img" aria-label="Screenshot of the marketplace web app dashboard with pie charts and data table"></div>
  <div class="portfolio-copy">
    <p class="eyebrow">Our Work</p>
    <h2 class="section-title">Portfolio</h2>
    <h3>Description: Secondary Marketplace Solution For Stone Fabricators And Design Professionals</h3>
    <p class="tags">Design, Consulting, Web App, Mobile App</p>
    <span class="btn">Read more</span>
  </div>
  <div class="arrows">
    <svg viewBox="0 0 34 14"><path d="M33 7H2M8 1 2 7l6 6" stroke="var(--orange)" stroke-width="2" fill="none"/></svg>
    <svg viewBox="0 0 34 14"><path d="M1 7h31M26 1l6 6-6 6" stroke="var(--ink)" stroke-width="2" fill="none"/></svg>
  </div>
</section>

<section class="section about">
  <div class="about-copy">
    <p class="eyebrow">About Us</p>
    <h2 class="section-title">Who We Are</h2>
    <p>Born technical entrepreneurs who aspire to bring their ideas to life. Businesses looking to implement strategic tech solutions, larger enterprises looking to roll out new initiatives, ideas to life. Businesses looking to implement strategic tech solutions, larger enterprises looking to roll out new initiatives.</p>
  </div>
  <div class="illustration art" role="img" aria-label="Illustration of developers collaborating around charts and a laptop"></div>
</section>

<section class="section approach">
  <h2 class="center-title">Our Approach</h2>
  <div class="illustration art" role="img" aria-label="Illustration of a developer coding at a desk with code windows"></div>
  <ul class="approach-list">
    <li><strong>Focus |</strong> We only play within our realm of excellence. Our team is deliberate about the work we take on and how we deliver it.</li>
    <li><strong>Quality over Quantity |</strong> We engage more deeply in fewer projects. Our small team aims to build fewer products to a higher standard, and we back every release we ship.</li>
    <li><strong>Entrepreneurial at Heart |</strong> Operating with a startup spirit and approach. We've founded companies of our own, so we think like owners and plan for growth.</li>
    <li><strong>Transferable Assets |</strong> Simple, effective execution makes products easy to pass on. Clean structure and clear documentation keep your team in control.</li>
  </ul>
</section>

<section class="section testimonials">
  <h2 class="center-title">Our Testimonial</h2>
  <p class="sub">Let's get testimonials from everyone (except for obviously)</p>
  <div class="cards">
    <div class="card">
      <svg class="quote" viewBox="0 0 18 14"><path d="M0 14V8C0 3 3 0 7 0v3C5 3 4 5 4 7h3v7zM11 14V8c0-5 3-8 7-8v3c-2 0-3 2-3 4h3v7z" fill="var(--orange)"/></svg>
      <p>Lorem ipsum dolor sit amet, consetetur sadipscing elitr, sed diam nonumy eirmod tempor invidunt ut labore et dolore magna aliquyam erat, sed diam voluptua. At vero eos et accusam et justo duo dolores et ea rebum.</p>
      <p class="who">Mara Ellison</p><p class="role">Founder</p><div class="stars">★★★★★</div>
    </div>
    <div class="card">
      <svg class="quote" viewBox="0 0 18 14"><path d="M0 14V8C0 3 3 0 7 0v3C5 3 4 5 4 7h3v7zM11 14V8c0-5 3-8 7-8v3c-2 0-3 2-3 4h3v7z" fill="var(--orange)"/></svg>
      <p>Lorem ipsum dolor sit amet, consetetur sadipscing elitr, sed diam nonumy eirmod tempor invidunt ut labore et dolore magna aliquyam erat, sed diam voluptua. At vero eos et accusam et justo duo dolores et ea rebum.</p>
      <p class="who">Owen Castell</p><p class="role">Director</p><div class="stars">★★★★★</div>
    </div>
    <div class="card">
      <svg class="quote" viewBox="0 0 18 14"><path d="M0 14V8C0 3 3 0 7 0v3C5 3 4 5 4 7h3v7zM11 14V8c0-5 3-8 7-8v3c-2 0-3 2-3 4h3v7z" fill="var(--orange)"/></svg>
      <p>Lorem ipsum dolor sit amet, consetetur sadipscing elitr, sed diam nonumy eirmod tempor invidunt ut labore et dolore magna aliquyam erat, sed diam voluptua. At vero eos et accusam et justo duo dolores et ea rebum.</p>
      <p class="who">Lena Hartwell</p><p class="role">CEO</p><div class="stars">★★★★★</div>
    </div>
  </div>
  <div class="arrows">
    <svg viewBox="0 0 34 14"><path d="M33 7H2M8 1 2 7l6 6" stroke="var(--orange)" stroke-width="2" fill="none"/></svg>
    <svg viewBox="0 0 34 14"><path d="M1 7h31M26 1l6 6-6 6" stroke="var(--ink)" stroke-width="2" fill="none"/></svg>
  </div>
</section>

<section class="section team">
  <h2 class="center-title">Executive Team</h2>
  <p class="intro">Lorem ipsum dolor sit amet, consetetur sadipscing elitr, sed diam nonumy eirmod tempor invidunt ut labore et dolore magna aliquyam erat, sed diam voluptua. At vero eos et accusam et justo duo dolores.</p>
  <div class="illustration photo" role="img" aria-label="Portrait photo of the cofounder in a suit"></div>
  <div class="member">
    <h4>Cofounder : Darius Venmoor, Cofounder</h4>
    <p>Darius is an Engineer, full-stack developer and award-winning entrepreneur. He was recognised and awarded by his regional business council as the top entrepreneurial voice. He is also the founder and technology lead for Kelpwarden, a SaaS solution recognised by the construction industry throughout North America.</p>
  </div>
  <div class="arrows">
    <svg viewBox="0 0 34 14"><path d="M33 7H2M8 1 2 7l6 6" stroke="var(--orange)" stroke-width="2" fill="none"/></svg>
    <svg viewBox="0 0 34 14"><path d="M1 7h31M26 1l6 6-6 6" stroke="var(--ink)" stroke-width="2" fill="none"/></svg>
  </div>
</section>

<section class="section cta">
  <h2>Start Your 14 Day Free Trial</h2>
  <p>Lorem ipsum dolor sit amet, consetetur sadipscing elitr, sed diam nonumy eirmod tempor invidunt ut labore et dolore magna aliquyam erat, sed diam voluptua.</p>
  <span class="btn btn-outline">Get Started</span>
</section>

<footer class="section footer">
  <svg class="shape" width="80" height="120" viewBox="0 0 80 120" aria-hidden="true"><path d="M0 20 40 0v40L0 60zM0 80l40-20v40L0 120z" fill="#f1f1f1"/></svg>
  <div class="foot-col foot-brand">
    <div class="brand"><span class="brand-mark"></span>BrambleForge</div>
    <p>Lorem ipsum dolor sit amet, consetetur sadipscing elitr, sed diam nonumy eirmod tempor invidunt ut labore et dolore magna.</p>
  </div>
  <div class="foot-col foot-links">
    <h4>Useful Links</h4>
    <p>Home<br>Who We Are<br>Team<br>Testimonials<br>Portfolio<br>Approach</p>
  </div>
  <div class="foot-col foot-contact">
    <h4>Contact Us</h4>
    <p>42 Quarry Lane,<br>Harlow, UK<br>+44 20 7946 0321<br>hello@brambleforge.dev</p>
  </div>
  <div class="foot-col foot-social">
    <h4>Social Links</h4>
    <div class="socials"><span></span><span></span><span></span></div>
  </div>
</footer>
<div class="section bottom-bar">© 2021 BrambleForge. All Rights Reserved</div>

</body>
</html>
```